KVR Inc Web Design

WHAT ARE WE DOING?
We are developing a new website look and feel for a new company called KVR Inc. This new look and feel should include colors, design elements, choice of photography and other imagery, fonts, and other user experience elements.

WHAT DO THEY DO?
KVR, Inc, makes tools for researchers who are studying protein-protein interactions. These molecules are the basic tools of biology, and serve as key targets for drug developers and disease researchers. The world of proteins is enormously complex, and companies like KVR provide researchers with critical tools that help them elucidate this world.

WHO ARE WE TALKING TO?
The target audience for this website are professional scientists working in university research or biopharma drug development. They are highly sophisticated consumers looking for key tools that will advance their research.

WHAT DO WE WANT THEM TO DO?
The site is an information resource for the customer exploring the tools that KVR sells and the scientific issues surrounding protein-protein interactions. They should be able to navigate easily to their content of choice, while the whole site should convey a professionalism that enhanced KVR’s credibility.

WHAT DOES THE KVR BRAND STAND FOR?
KVR stands for illumination. Proteins are challenging to study, and KVR exists to help shed light on their workings.

WHAT ARE THE KEY VALUES OF THE KVR BRAND?
Integrity. Innovation. Insight.

WHAT ARE THE EXECUTIONAL MANDITORIES?
The look and feel is completely up for grabs. Nothing is off the table.

WHAT ARE THE DELIVERABLES?
We need new designs for the following templates:
http://cms.marlowbench.com/
http://cms.marlowbench.com/products-and-services/instruments-3/bench-top-instruments/
http://cms.marlowbench.com/category/lab-study/

```html
<!DOCTYPE html>
<html lang="en">
<head>
<meta charset="utf-8">
<title>Pipettes – KVR Inc</title>
<link rel="stylesheet" href="https://fonts.googleapis.com/css2?family=Figtree:ital,wght@0,400;0,600;0,700;1,600&family=Open+Sans:wght@400&display=swap">
<style>
  :root {
    --orange: #fcb445;
    --orange-text: #fbb040;
    --brown: #5c4830;
    --ink: #222;
    --body: #555;
    --rule: #cfcfcf;
    --tab-bg: #e3e2e2;
    --link-blue: #39a9d8;
  }
  * { box-sizing: border-box; margin: 0; padding: 0; }
  html, body { width: 1191px; height: 1200px; overflow: hidden; background: #fff; }
  body { position: relative; font-family: "Figtree", sans-serif; color: var(--body); }
  .abs { position: absolute; }

  .site-header { left: 0; top: 0; width: 1191px; height: 65px; background: var(--orange); }
  .brand { left: 159px; top: 14px; font-size: 28px; font-weight: 400; color: #fff; letter-spacing: 6px; line-height: 36px; }
  .main-nav a { position: absolute; top: 17px; height: 28px; line-height: 28px; color: #fff; font-weight: 700; font-size: 14.5px; text-decoration: none; }
  .main-nav a.active { background: var(--brown); border-radius: 14px; padding: 0 12px; }
  .search { left: 905px; top: 20px; width: 125px; height: 22px; background: #e4a238; color: #fff; font-size: 11px; line-height: 22px; padding-left: 7px; }
  .search svg { position: absolute; right: 5px; top: 5px; }

  .page-title { left: 158px; top: 100px; font-size: 25px; font-weight: 400; color: var(--ink); }
  .title-rule { left: 159px; top: 135px; width: 872px; height: 3px; border-top: 1px solid var(--rule); border-bottom: 1px solid var(--rule); }

  .sidebar { left: 159px; top: 156px; width: 201px; height: 461px; border: 1px solid #ddd; box-shadow: 0 1px 2px rgba(0,0,0,.2); background: #fff; }
  .side-head { position: absolute; left: 0; width: 199px; height: 37px; background: var(--brown); color: #fff; font-weight: 700; font-size: 16px; line-height: 37px; padding-left: 16px; }
  .side-menu a { position: absolute; left: 0; width: 199px; height: 30px; line-height: 30px; padding-left: 29px; font-size: 14px; color: #111; text-decoration: none; }
  .side-menu a::before { content: "›"; position: absolute; left: 17px; font-weight: 700; }
  .side-menu a.current { background: var(--orange); color: #fff; }
  .news-item { position: absolute; left: 17px; width: 170px; font-size: 11.5px; line-height: 15.3px; color: #333; }
  .news-item time { display: block; font-style: italic; font-weight: 600; color: #555; }
  .news-sep { position: absolute; left: 0; width: 199px; border-top: 1px solid #e6e6e6; }

  .hero { left: 383px; top: 157px; width: 648px; height: 271px; border: 1px solid #ddd; }
  .hero-photo { position: absolute; left: 5px; top: 5px; width: 440px; height: 260px; background: linear-gradient(90deg, #b8c4cc 0%, #dfe5e8 55%, #fff 100%); }
  .hero-quote { position: absolute; left: 428px; top: 48px; width: 210px; font-size: 21.5px; font-weight: 700; line-height: 23.4px; color: var(--orange-text); }

  .copy { left: 383px; width: 648px; font-size: 12px; line-height: 18.7px; }
  .copy a, .tab-text a { color: var(--orange-text); text-decoration: none; }

  .tabs { left: 383px; top: 727px; width: 647px; height: 311px; border: 1px solid #ddd; }
  .tab { position: absolute; top: 0; height: 32px; line-height: 32px; background: var(--tab-bg); color: #444; font-size: 14.5px; font-weight: 600; text-align: center; border-right: 1px solid #fff; }
  .tab.active { background: #fff; color: var(--link-blue); }
  .tab-photo-frame { position: absolute; left: 21px; top: 54px; width: 232px; height: 232px; border: 1px solid #ddd; padding: 5px; }
  .tab-photo { width: 220px; height: 220px; background: linear-gradient(135deg, #3b6fb8, #1f3f78 60%, #6a5a4a); }
  .tab-text { position: absolute; left: 263px; top: 64px; width: 370px; font-size: 12px; line-height: 17px; }

  .footer-rule { left: 159px; top: 1063px; width: 872px; height: 3px; border-top: 1px solid var(--rule); border-bottom: 1px solid var(--rule); }
  .footer-mark { left: 583px; top: 1088px; width: 25px; height: 2px; background: linear-gradient(90deg, var(--orange) 0 45%, var(--brown) 45% 55%, var(--orange) 55%); }
  .footer-nav { left: 0; top: 1102px; width: 1191px; text-align: center; font-family: "Open Sans", sans-serif; font-size: 11px; color: #444; }
  .copyright { left: 0; top: 1121px; width: 1191px; text-align: center; font-family: "Open Sans", sans-serif; font-size: 12px; color: #444; }
  .social { left: 565px; top: 1143px; display: flex; gap: 4px; }
  .social span { width: 18px; height: 18px; border-radius: 50%; background: #555; display: block; }
</style>
</head>
<body>
  <header class="site-header abs">
    <div class="brand abs">KVR INC</div>
    <nav class="main-nav">
      <a style="left:328px">Company</a>
      <a class="active" style="left:400px">Products &amp; Services</a>
      <a style="left:561px">Learning Center</a>
      <a style="left:686px">Events</a>
      <a style="left:750px">KVR News</a>
      <a style="left:833px">Contact</a>
    </nav>
    <div class="search abs">Search
      <svg width="12" height="12" viewBox="0 0 12 12"><circle cx="5" cy="5" r="3.5" fill="none" stroke="#f4d29a" stroke-width="1.4"/><line x1="7.5" y1="7.5" x2="11" y2="11" stroke="#f4d29a" stroke-width="1.6"/></svg>
    </div>
  </header>

  <h1 class="page-title abs">PIPETTES</h1>
  <div class="title-rule abs"></div>

  <aside class="sidebar abs">
    <div class="side-head" style="top:0">Product Overview</div>
    <nav class="side-menu">
      <a style="top:39px">Reagents</a>
      <a class="current" style="top:75px">Pipettes</a>
      <a style="top:111px">Tubes</a>
    </nav>
    <div class="side-head" style="top:156px">Latest News</div>
    <div class="news-item" style="top:209px"><time>October 7, 2013</time>Lorem ipsum dolor sit amet, consect etureius mod dipisi cing elit, sed do eiusmod tempor mod &gt;&gt;&gt;</div>
    <div class="news-sep" style="top:298px"></div>
    <div class="news-item" style="top:308px"><time>October 7, 2013</time>Lorem ipsum dolor sit amet, consect etureius mod dipisi cing elit, sed do eiusmod tempor mod &gt;&gt;&gt;</div>
  </aside>

  <section class="hero abs">
    <div class="hero-photo" role="img" aria-label="Three scientists in lab coats and safety glasses working at a microscope"></div>
    <p class="hero-quote">Donec non massa lacinia, commodo eros eget, id rutrum arcu. Integer velit eleifend congue, massa consequat mauris!</p>
  </section>

  <p class="copy abs" style="top:455px">Quisque feugiat lacus vitae posuere blandit. Nulla sit amet laoreet felis, id rhoncus nisl. Aenean fringilla quam in nibh egestas, in malesuada tortor accumsan. Donec non massa lacinia, commodo eros eget, rutrum arcu. Integer tincidunt, velit id eleifend congue, odio massa consequat mauris, a scelerisque nulla nulla eu nulla. Cras luctus pulvinar nibh ut viverra. Aenean vestibulum vitae justo non dictum. Mauris ut tellus in dui pretium dictum nec non tortor. Nulla a velit quis dolor interdum scelerisque eu et nisl.</p>
  <p class="copy abs" style="top:567px">Donec auctor mollis ligula eget molestie. Aliquam erat volutpat. Curabitur sapien libero, condimentum ac nisl ultricies tincidunt ipsum. Donec in iaculis metus. Mauris eleifend nisi non sapien commodo, hendrerit consectetur. Pellentesque faucibus, purus non dictum lacinia, ante augue pretium neque, vitae egestas dui nisl et enim. ornare Suspendisse nibh vel lacinia rhoncus Donec auctor mollis ligula eget molestie. Pellentesque faucibus, purus non dictum lacinia, ante augue pretium neque, <a>vitae egestas</a> dui nisl et enim. Suspendisse iaculis nibh vel lacinia rhoncus Donec non massa lacinia, commodo eros eget, rutrum arcu. Integer tincidunt, velit id eleifend congue, odio massa consequat mauris, a scelerisque nulla nulla eu nulla. Cras luctus pulvinar nibh ut viverra. Aenean vestibulum vitae justo non dictum.</p>

  <section class="tabs abs">
    <div class="tab active" style="left:0;width:128px">Overview</div>
    <div class="tab" style="left:128px;width:130px">Features</div>
    <div class="tab" style="left:258px;width:153px">Specifications</div>
    <div class="tab" style="left:411px;width:114px">FAQ's</div>
    <div class="tab" style="left:525px;width:121px;border-right:0">Manuals</div>
    <div class="tab-photo-frame"><div class="tab-photo" role="img" aria-label="Gloved hands holding a pipette over a test tube"></div></div>
    <div class="tab-text">
      <p>Quisque feugiat lacus vitae posuere blandit. Nulla sit amet laoreet felis, id rhoncus nisl. Aenean fringilla quam in nibh egestas, in malesuada tortor accumsan. Donec non massa lacinia, commodo eros eget, rutrum arcu. Integer tincidunt, velit id eleifend congue, odio massa consequat mauris, a scelerisque nulla nulla eu nulla. Cras luctus pulvinar nibh ut viverra. Aenean vestibulum vitae justo non dictum. Mauris ut tellus in dui pretium dictum nec non tortor. Nulla a velit quis dolor interdum <a>scelerisque</a> eu et nisl.</p>
      <p style="margin-top:17px">Donec auctor mollis ligula eget molestie. Aliquam erat volutpat. Curabitur sapien libero, condimentum ac nisl nec, ultricies tincidunt ipsum. Donec in iaculis metus. Mauris eleifend nisi non sapien commodo, hendrerit ornare lacus consectetur.</p>
    </div>
  </section>

  <footer>
    <div class="footer-rule abs"></div>
    <div class="footer-mark abs"></div>
    <nav class="footer-nav abs">Company &nbsp;-&nbsp; Products &amp; Services &nbsp;-&nbsp; Learning Center &nbsp;-&nbsp; Events &nbsp;-&nbsp; KVR News &nbsp;-&nbsp; Contact</nav>
    <p class="copyright abs">Copyright © KVR Inc. 2013</p>
    <div class="social abs"><span></span><span></span><span></span></div>
  </footer>
</body>
</html>
```